Business Cards Needed for Innovative Healthcare Marketing Company

We are a marketing company focused on healthcare. Our company is all about rebranding yourself renewing your image and generating results. The phoenix stands for "reborn" or "rising" which we provide new brands for our clients we take their old brands and renew it with creativity and innovation. I am looking for a business card with color dimension. I have attached an example of a card I think has the look and feel of what I am trying to accomplish. I like that the card example has black and grey font colors, I like the font placement and the small logo, I really like the use of the colors on the right those are the colors of my logo. My logo is phoenix so maybe incorporating flames similar to that design. I would like the back a solid color maybe red with an opaque version of the logo and website. As a marketing company I am always open to creative liberty!

Target Market(s)

Doctors and business professionals.

Industry/Entity Type

Marketing

Contact Information for Business Card

Valcorne Health Care Marketing
Marla Tenwick- CEO
#(512)638-2974
email-marla@valcorne.com
website- valcorne.com

Font styles to use
Sans Serif

Colors
ec1f27
f37122
ffc214
fbed22
fbf289
f04a50

Requirements
Must have
• The logo and required information
Nice to have
• icons by the information
Should not have
• child like font

```html
<!DOCTYPE html>
<html lang="en">
<head>
<meta charset="utf-8">
<title>Valcorne Health Care Marketing — Business Card</title>
<link rel="stylesheet" href="https://fonts.googleapis.com/css2?family=Open+Sans:wght@300;400;700&display=swap">
<style>
  :root {
    --stage-top: #262626;
    --stage-bottom: #050505;
    --card-white: #ffffff;
    --brand-red: #a11f24;
    --brand-red-deep: #8f1a1f;
    --brand-orange: #f7941d;
    --mark-orange: #e8651f;
    --name-red: #8e1b1f;
    --ink: #2b2b2b;
    --on-red: #ffffff;
  }
  * { margin: 0; padding: 0; box-sizing: border-box; }
  html, body { width: 1200px; height: 900px; overflow: hidden; }
  body {
    background: linear-gradient(180deg, var(--stage-top) 0%, #151515 60%, var(--stage-bottom) 100%);
    font-family: "Open Sans", Arial, sans-serif;
    position: relative;
  }
  .card {
    position: absolute;
    top: 306px;
    width: 440px;
    height: 271px;
    border-radius: 12px;
    overflow: hidden;
    box-shadow: 0 6px 18px rgba(0,0,0,0.55);
  }
  .card-front { left: 149px; background: var(--card-white); }
  .card-back { left: 608px; }

  .front-mark {
    position: absolute;
    left: 40px;
    top: 110px;
    width: 152px;
    text-align: center;
    font-size: 24px;
    font-weight: 700;
    color: var(--mark-orange);
    letter-spacing: 0.5px;
  }
  .holder {
    position: absolute;
    left: 246px;
    top: 76px;
  }
  .holder-name {
    font-size: 16.5px;
    font-weight: 700;
    color: var(--name-red);
    letter-spacing: 0.2px;
    line-height: 1.1;
  }
  .holder-title {
    font-size: 11.5px;
    color: var(--ink);
    margin-top: 2px;
  }
  .contact-list {
    position: absolute;
    left: 246px;
    top: 139px;
    list-style: none;
  }
  .contact-list li {
    display: flex;
    align-items: center;
    font-size: 12px;
    color: var(--ink);
    height: 16px;
  }
  .contact-list svg { width: 8px; height: 8px; margin-right: 7px; fill: var(--name-red); }
  .front-bands { position: absolute; left: 0; bottom: 0; }

  .back-field {
    position: absolute;
    inset: 0;
    background: radial-gradient(ellipse at center, #a92227 0%, var(--brand-red) 55%, var(--brand-red-deep) 100%);
  }
  .back-name {
    position: absolute;
    left: 0; right: 0;
    top: 94px;
    text-align: center;
    color: var(--on-red);
    font-weight: 300;
    line-height: 1.1;
  }
  .back-name .word { display: block; font-size: 46px; letter-spacing: 1px; }
  .back-name .line { display: block; font-size: 16.5px; letter-spacing: 0.6px; margin-top: 8px; }
</style>
</head>
<body>
  <section class="card card-front">
    <div class="front-mark">Valcorne</div>
    <div class="holder">
      <div class="holder-name">MARLA TENWICK</div>
      <div class="holder-title">CEO</div>
    </div>
    <ul class="contact-list">
      <li><svg viewBox="0 0 10 10"><path d="M1 3.5 Q1 1.5 3 1.5 L7 1.5 Q9 1.5 9 3.5 L7.5 4.2 L6.8 3.2 L3.2 3.2 L2.5 4.2 Z M2.5 5 L7.5 5 L8.5 8.5 L1.5 8.5 Z"/></svg>(512)638-2974</li>
      <li><svg viewBox="0 0 10 10"><path d="M0.5 2 L9.5 2 L9.5 8.5 L0.5 8.5 Z M1 2.5 L5 5.5 L9 2.5" stroke="#fff" stroke-width="0.8"/></svg>marla@valcorne.com</li>
      <li><svg viewBox="0 0 10 10"><circle cx="5" cy="5" r="4.5"/></svg>www.valcorne.com</li>
    </ul>
    <svg class="front-bands" width="440" height="30" viewBox="0 0 440 30">
      <polygon points="0,0 244,0 232,30 0,30" fill="var(--brand-orange)"/>
      <polygon points="251,5 440,5 440,30 240,30" fill="var(--brand-red)"/>
    </svg>
  </section>

  <section class="card card-back">
    <div class="back-field" role="img" aria-label="Deep red field with a faint repeating brand pattern"></div>
    <div class="back-name">
      <span class="word">VALCORNE</span>
      <span class="line">HEALTH CARE MARKETING</span>
    </div>
  </section>
</body>
</html>
```